Financial Services Consultant needs a business card

We need a business card for a new consulting company based in Melbourne called
"Quelbrook Insights". Tagline is Measure, Monitor, Save
We would like to see business card designs that are in line with the minimal style of the website www.quelbrook-insights.example
The font I have used on the website is Proxima Nova and would like the same or similar font used on the business card with a minimal design in line with the website Two sided with "QUELBROOK INSIGHTS" MEASURE, MONITOR, SAVE on one side and name, title and contact details on the otther
Updates

Hi All, thanks for your submissions, much appreciated.

I have recently added some colour to my webiste, it is hex #3a7b74 for those that wish to use it
Thanks

Hi all

thanks very much for your design submissions I am very impressed and they are much appreciated.

Interms of general feedback please find below;

Colour: I am trying to stick to a minimal design and colour scheme for my website which is still under construction, up to 3 colours( www.quelbrook-insights.example) it is currently black and white with a small amount of blue/green but I am open to suggestion/interpretations for a consulting company.

Card: I dont mind if it has rounded edges or straight, I was thinking about using a letterpress card if possible

Detail: the detail on the card will include; Name, Title, Mobile, Personal Email, Business Email,Web,Business Address

Once again thanks for submissions

Industry/Entity Type

Business

```html
<!DOCTYPE html>
<html lang="en">
<head>
<meta charset="utf-8">
<title>Quelbrook Insights — Business Card</title>
<link rel="stylesheet" href="https://fonts.googleapis.com/css2?family=Montserrat:wght@700&family=Open+Sans:wght@400;600;700&display=swap">
<style>
  :root {
    --canvas-bg: #e6e6ea;
    --card-bg: #ffffff;
    --ink: #111111;
    --text-grey: #4a4a4a;
    --teal: #3a7b74;
    --band: #1a1716;
    --card-shadow: rgba(0, 0, 0, 0.18);
  }
  * { margin: 0; padding: 0; box-sizing: border-box; }
  html, body { width: 1200px; height: 987px; overflow: hidden; }
  body {
    background: var(--canvas-bg);
    font-family: "Open Sans", Arial, sans-serif;
    color: var(--text-grey);
    position: relative;
  }
  .card {
    position: absolute;
    left: 280px;
    width: 640px;
    height: 366px;
    background: var(--card-bg);
    border-radius: 28px;
    box-shadow: 0 8px 24px var(--card-shadow);
    overflow: hidden;
  }
  .card--brand { top: 96px; }
  .card--contact { top: 525px; }

  .wordmark {
    font-family: "Montserrat", Arial, sans-serif;
    font-weight: 700;
    color: var(--ink);
    letter-spacing: 0.12em;
    white-space: nowrap;
  }
  .card--brand .wordmark {
    position: absolute;
    top: 108px;
    left: 0; right: 0;
    text-align: center;
    font-size: 36px;
  }
  .tagline {
    position: absolute;
    top: 210px;
    left: 0; right: 0;
    text-align: center;
    font-size: 19px;
    color: var(--text-grey);
  }
  .brand-web {
    position: absolute;
    top: 244px;
    left: 0; right: 0;
    text-align: center;
    font-size: 18px;
    letter-spacing: 0.28em;
    color: var(--text-grey);
  }
  .brand-web strong { color: var(--ink); font-weight: 700; }

  .card--contact .wordmark {
    position: absolute;
    top: 34px;
    left: 36px;
    font-size: 27px;
  }
  .person {
    position: absolute;
    top: 118px;
    left: 36px;
    font-size: 19px;
  }
  .person__name { font-weight: 700; color: var(--text-grey); }
  .person__title { color: var(--teal); }
  .phone {
    position: absolute;
    top: 152px;
    left: 36px;
    font-size: 16px;
    display: flex;
    align-items: center;
    gap: 7px;
  }
  .phone svg { width: 14px; height: 14px; }
  .rule {
    position: absolute;
    left: 0; right: 0;
    height: 1.5px;
    background: var(--teal);
  }
  .rule--top { top: 226px; }
  .rule--bottom { top: 282px; }
  .band {
    position: absolute;
    top: 232px;
    left: 0; right: 0;
    height: 44px;
    background: var(--band);
    display: flex;
    align-items: center;
    padding-left: 36px;
    color: #ffffff;
    font-size: 16px;
  }
  .address {
    position: absolute;
    top: 300px;
    left: 36px;
    font-size: 17px;
    color: var(--text-grey);
  }
</style>
</head>
<body>
  <section class="card card--brand" aria-label="Card front">
    <div class="wordmark">QUELBROOK INSIGHTS</div>
    <p class="tagline">Measure, Monitor, Save</p>
    <p class="brand-web">www.<strong>quelbrook-insights</strong>.example</p>
  </section>

  <section class="card card--contact" aria-label="Card back">
    <div class="wordmark">QUELBROOK INSIGHTS</div>
    <p class="person"><span class="person__name">Your Name,</span> <span class="person__title">Title</span></p>
    <p class="phone">
      <svg viewBox="0 0 24 24" aria-hidden="true"><path fill="none" stroke="#4a4a4a" stroke-width="2" d="M6.6 2.5l3 3.2-1.9 2.6c1.3 2.9 3.4 5 6.3 6.3l2.6-1.9 3.2 3-1.8 3.6C10.4 19.3 4.7 13.6 3 6.4z"/></svg>
      123-456-0789
    </p>
    <div class="rule rule--top"></div>
    <div class="band">www.quelbrook-insights.example</div>
    <div class="rule rule--bottom"></div>
    <p class="address">Street Name, City Name, State Zip Code</p>
  </section>
</body>
</html>
```